Moxy Fen needs some awesome stationary

Do you have what it takes to get my brand? You either do or you don't, have a crack at a design and you my just win my business.

I don't want to waste your or my time, so put your creative genius on either a business card or envelope.

I however need a package of stationary that follows the same brand. I will message you to complete the remaining should I like your first submission.

Here is what I need, have a go!

Basically I need the following for my small business based in melbourne.
- Letterhead (printer ready and MS Word)
- Business Card
- Compliments Slip
- Envelope
- Proposal Cover Page (MS Word only)
- Presentation Folder
- Marbled Fox Cards
- Student Name Tent
- Index Cards
- Vell-Ka

I am establishing the brand and it must be modern, professional but also relaxed; that is not formal and not corporate. It represents a company are leaders, but small enough to care and operate like a bunch of friends. We are bringing people and conversations back to business, and turfing out all the bureaucracy and crazy and wasteful procedures. Its about "lets talk and figure it out together and find even better ways".

Target Market(s)

Mainly companies that build software products, but Agile practices are used in many other industries (even graphic design projects)

Industry/Entity Type

Information Technology

Font styles to use
Sans Serif

Colors
3176b5
aaaaaa

Requirements
Must have
• I like curves and circles and not boxes or rectangles.
• I want a colour rich design with my brand colours, but it must be balanced.
• I want more modern than traditional, but simple modern
Should not have
• Not corporate
• Please don't waste my time if your not going to think about it.
• Don't mess with my primary logo
• Don't change my colours
• Don't overlay logo on image

```html
<!DOCTYPE html>
<html lang="en">
<head>
<meta charset="utf-8">
<title>Moxy Fen Business Card</title>
<link href="https://fonts.googleapis.com/css2?family=Open+Sans:wght@400;600;700&display=swap" rel="stylesheet">
<style>
  :root {
    --brand-blue: #3a62a8;
    --brand-grey: #8e98a8;
    --light-grey: #aab2bf;
    --text-grey: #8a8f98;
    --ink: #3a3f47;
    --paper: #ffffff;
    --backdrop: #ece9e4;
  }
  * { margin: 0; padding: 0; box-sizing: border-box; }
  html, body { width: 1200px; height: 950px; overflow: hidden; }
  body {
    background: var(--backdrop);
    font-family: "Open Sans", sans-serif;
    display: flex; flex-direction: column; align-items: center; justify-content: center;
    gap: 50px;
  }
  .card {
    position: relative;
    width: 700px; height: 400px;
    border-radius: 32px;
    overflow: hidden;
    box-shadow: 0 6px 18px rgba(0,0,0,.18);
  }
  .card-front { background: var(--paper); }
  .card-back { background: var(--brand-grey); }

  .front-band { position: absolute; left: 0; bottom: 0; width: 700px; height: 70px; }
  .band-web {
    position: absolute; right: 36px; bottom: 18px;
    color: #fff; font-size: 17px; letter-spacing: .5px;
  }

  .brand {
    position: absolute; right: 48px; top: 44px;
    display: flex; align-items: center; gap: 14px;
  }
  .brand-dot { width: 58px; height: 58px; border-radius: 50%; background: var(--brand-blue); }
  .brand-name { font-size: 44px; font-weight: 700; color: var(--brand-blue); line-height: 1; }

  .divider {
    position: absolute; left: 44px; right: 44px; top: 148px;
    height: 1px; background: var(--light-grey);
  }

  .person { position: absolute; left: 44px; top: 168px; }
  .person-name { font-size: 25px; font-weight: 700; color: var(--brand-blue); }
  .person-role { font-size: 17px; color: var(--text-grey); margin-top: 2px; }

  .contacts { position: absolute; left: 44px; top: 236px; list-style: none; }
  .contacts li {
    display: flex; align-items: center; gap: 10px;
    font-size: 16px; color: var(--ink); line-height: 25px;
  }
  .contacts svg { width: 15px; height: 15px; flex: none; }

  .address {
    position: absolute; right: 48px; top: 176px;
    text-align: right; font-size: 18px; color: var(--ink); line-height: 26px;
  }

  .back-brand {
    position: absolute; left: 50%; top: 50%; transform: translate(-50%, -50%);
    display: flex; align-items: center; gap: 14px;
  }
  .back-dot { width: 54px; height: 54px; border-radius: 50%; background: #fff; }
  .back-name { font-size: 40px; font-weight: 700; color: #fff; line-height: 1; }
  .back-web {
    position: absolute; left: 50%; bottom: 40px; transform: translateX(-50%);
    color: #fff; font-size: 17px; letter-spacing: .5px;
  }
</style>
</head>
<body>

  <section class="card card-front" aria-label="Business card front">
    <div class="brand">
      <span class="brand-dot"></span>
      <span class="brand-name">Moxy Fen</span>
    </div>

    <div class="divider"></div>

    <div class="person">
      <p class="person-name">Dane Colwell</p>
      <p class="person-role">CEO, Professional Agile Trainer</p>
    </div>

    <ul class="contacts">
      <li>
        <svg viewBox="0 0 16 16"><path d="M3 1.5 L6 1 L7.3 4.6 L5.5 6 C6.3 7.8 8.2 9.7 10 10.5 L11.4 8.7 L15 10 L14.5 13 C14.3 14.2 13.2 15 12 14.8 C6.5 14 2 9.5 1.2 4 C1 2.8 1.8 1.7 3 1.5Z" fill="var(--ink)"/></svg>
        1300MOXYFEN
      </li>
      <li>
        <svg viewBox="0 0 16 16"><rect x="4" y="1" width="8" height="14" rx="1.5" fill="none" stroke="var(--ink)" stroke-width="1.6"/><circle cx="8" cy="12.5" r="0.9" fill="var(--ink)"/></svg>
        +61 400 555 017
      </li>
      <li>
        <svg viewBox="0 0 16 16"><rect x="1" y="3" width="14" height="10" rx="1" fill="var(--brand-blue)"/><path d="M1.5 3.8 L8 9 L14.5 3.8" fill="none" stroke="#fff" stroke-width="1.3"/></svg>
        dane@moxy-fen.com.au
      </li>
    </ul>

    <address class="address" style="font-style: normal;">
      PO Box 4410<br>
      Larkfield East<br>
      VIC 3199, Australia
    </address>

    <svg class="front-band" viewBox="0 0 700 70" preserveAspectRatio="none">
      <path d="M0 46 L300 46 C330 46 340 14 370 14 L700 14 L700 70 L0 70 Z" fill="var(--brand-blue)"/>
      <path d="M0 54 L306 54 C338 54 348 22 378 22 L700 22 L700 70 L0 70 Z" fill="var(--light-grey)"/>
    </svg>
    <span class="band-web">www.moxy-fen.com.au</span>
  </section>

  <section class="card card-back" aria-label="Business card back">
    <div class="back-brand">
      <span class="back-dot"></span>
      <span class="back-name">Moxy Fen</span>
    </div>
    <span class="back-web">www.moxy-fen.com.au</span>
  </section>

</body>
</html>
```